Web and Logo Design for eCommerce site

We're launching a sister brand and require a full design for the site.

The site must have an established feel and appeal to corporate and institutional buyers.
Updates

Just a note about the wireframe design:

The Search & Rescue / Coast Guard / NVDK, etc. in the header area aren't buttons or menu items, but rather just info (along the lines of a tagline).  Sort of a "who we serve" sort of thing.

Worth noting is that it's specifically geared towards LARGE BUYERS.  For example, a police force buying 200 headlamps and 85 pairs of gloves.  So they'll register + sign in and then add a bunch of items to a RFQ.

Aim for a professional, masculine design.

Target Market(s)

We will be selling outdoor gear to the military, law enforcement, fire and rescue and first responders.

Requirements
Must have
• We require:
- Logo (vector based)

Site:
- template page
* main site template, re-skinned version of our current site
* horizontal drop-down menu
- product listings page
* thumbnail view of products
- product details page
* including elements such as product image, color/size selector, descriptions and specs (again, based loosely on our current website)
- account management page
* illustrating basic data entry styles for text box, buttons, grid, etc.

The site needs to be given a responsive design, so 2 versions of each design should be presented for desktop + mobile views.

Additional funds are available if the designer is able to fully implement the designs into a responsive framework such as bootstrap.

Nice to have
• Clean, professional design similar to:

http://military.trailvexagear.com/gov/accessories/gloves.html

http://leaf.ombrivo.com/ProductFind.aspx?language=EN&category=Hardshell&subcat=Waterproof_Jackets

```html
<!DOCTYPE html>
<html lang="en">
<head>
<meta charset="utf-8">
<title>Northvale – Outdoor Pro Supply</title>
<link href="https://fonts.googleapis.com/css2?family=Arimo:wght@400;700&display=swap" rel="stylesheet">
<style>
:root{
  --green:#3f9a12;--green-light:#6cc12a;--green-dark:#2f7c0b;
  --grey-bar:#efefef;--text:#333;--muted:#999;--line:#ddd;
  --footer:#5b5b5b;--footer-dark:#4a4a4a;--side-head:#777;
}
*{margin:0;padding:0;box-sizing:border-box}
html,body{width:726px;height:1200px;overflow:hidden;background:#fff}
body{position:relative;font-family:"Arimo",Arial,sans-serif;color:var(--text)}
.abs{position:absolute}
.brandmark{left:87px;top:24px}
.brandmark-row{display:flex;align-items:center;gap:7px}
.brandmark-row i{display:block;width:13px;height:13px;background:var(--green)}
.brandmark-name{font-size:19px;font-weight:400;color:var(--text);line-height:1}
.brandmark-sub{font-size:7px;color:#555;margin-top:5px}
.tagline{right:85px;top:31px;text-align:center;font-size:8.5px;line-height:13px;color:#555}
.serve{top:71px;left:0;width:726px;height:29px;background:var(--grey-bar);display:flex;justify-content:center;align-items:center;gap:13px;font-size:7.5px;color:#333}
.mainnav{top:100px;left:0;width:726px;height:30px;background:linear-gradient(#6cc12a,#3f9a12);display:flex;padding-left:87px}
.mainnav a{color:#fff;text-decoration:none;font-size:8px;height:30px;display:flex;align-items:center;justify-content:center;border-right:1px solid rgba(255,255,255,.25);padding:0 20px}
.mainnav a:last-child{border:none}
.hero{top:130px;left:0;width:726px;height:269px;background:linear-gradient(100deg,#5f5a52 0%,#8a8780 22%,#dfe7ee 40%,#eef3f8 70%,#c9d6e3 100%)}
.dots{top:386px;left:581px;display:flex;gap:4px}
.dots i{width:8px;height:8px;border-radius:50%;background:#333;display:block}
.dots i:first-child{background:var(--green)}
.sidebar{top:419px;left:86px;width:158px;height:427px;border:1px solid #ccc;background:#f4f4f4}
.sidebar h2{height:27px;background:linear-gradient(#8a8a8a,#6d6d6d);color:#fff;font-size:11.5px;font-weight:400;padding:8px 9px}
.sidebar ul{list-style:none;padding:6px 0 0 9px}
.sidebar li{font-size:7.5px;color:#666;height:22.7px;display:flex;align-items:center;gap:8px}
.sidebar svg{width:8px;height:8px}
.latest{top:425px;left:258px;font-size:11px;color:#333}
.arrows{top:421px;left:619px}
.card{width:119px;height:191px;border:1px solid #ddd;text-align:center}
.thumb{width:64px;height:68px;margin:6px auto 0;border-radius:6px}
.card h3{font-size:8px;font-weight:400;color:#555;margin-top:11px}
.card p{font-size:6.5px;color:#aaa;line-height:13px;margin-top:6px;padding:0 6px}
.price{font-size:11.5px;color:#333;margin-top:5px}
.cart{display:inline-flex;align-items:center;gap:8px;margin-top:8px;background:linear-gradient(#58b51e,#2f860b);color:#fff;font-size:7.5px;padding:0 8px;height:25px;border-radius:4px}
.brands-title{top:874px;left:0;width:726px;text-align:center;font-size:11px;color:#333}
.brands{top:902px;left:85px;width:556px;height:66px;border:1px solid #ddd;box-shadow:0 1px 2px rgba(0,0,0,.1);display:flex;align-items:center;justify-content:space-around;padding:0 12px}
.brand{display:flex;align-items:center;gap:4px;font-size:10px;font-weight:700}
.brand i{display:block;width:11px;height:11px}
.footer{top:1005px;left:0;width:726px;height:166px;background:var(--footer);color:#fff}
.fcol{position:absolute;top:17px}
.fcol h4{font-size:10px;font-weight:400;margin-bottom:8px}
.fcol li{list-style:none;font-size:6.5px;line-height:16.5px}
.fcol p{font-size:6.5px;line-height:15px}
.field{width:125px;height:19px;background:#fff;border-radius:4px;color:#555;font-size:6.5px;padding:6px 7px;margin-top:6px}
.submit{margin:5px 0 0 67px;width:58px;height:19px;background:#fff;border-radius:4px;color:#444;font-size:7.5px;text-align:center;line-height:19px}
.social{display:flex;align-items:center;gap:10px;font-size:6.5px;height:21px}
.social i{width:17px;height:17px;border-radius:50%;background:#fff;display:block}
.copy{top:1171px;left:0;width:726px;height:29px;background:var(--footer-dark);color:#fff;font-size:6.5px;text-align:center;line-height:29px}
</style>
</head>
<body>
<header>
  <div class="abs brandmark"><div class="brandmark-row"><i></i><span class="brandmark-name">Northvale</span></div><div class="brandmark-sub">Canada Outdoor Pro Supply</div></div>
  <div class="abs tagline">Great Outdoor Gear for<br>canada's First Responders</div>
</header>
<div class="abs serve"><span>SEARCH &amp; RESUCE</span>/<span>COAST&nbsp; GUARD</span>/<span>NVDK</span>/<span>FIRE</span>/<span>MILITARY</span>/<span>LAW ENFORCEMENT</span></div>
<nav class="abs mainnav"><a>Rescue Gear</a><a>Footwear</a><a>Clothing</a><a>Sleeping Bags</a><a>Camping Gear</a><a>Snow Sports</a><a>Brands</a></nav>
<div class="abs hero" role="img" aria-label="Climber ascending a snowy mountain slope with ice axes and ropes"></div>
<div class="abs dots"><i></i><i></i><i></i><i></i></div>

<aside class="abs sidebar">
  <h2>CATEGORY</h2>
  <ul>
    <li><svg viewBox="0 0 10 10"><path d="M1 5l3 3 5-7" stroke="#666" stroke-width="1.6" fill="none"/></svg>Backpacks</li>
    <li><svg viewBox="0 0 10 10"><path d="M1 5l3 3 5-7" stroke="#666" stroke-width="1.6" fill="none"/></svg>Shelters</li>
    <li><svg viewBox="0 0 10 10"><path d="M1 5l3 3 5-7" stroke="#666" stroke-width="1.6" fill="none"/></svg>Camo Kitchen</li>
    <li><svg viewBox="0 0 10 10"><path d="M1 5l3 3 5-7" stroke="#666" stroke-width="1.6" fill="none"/></svg>Sleep Department</li>
    <li><svg viewBox="0 0 10 10"><path d="M1 5l3 3 5-7" stroke="#666" stroke-width="1.6" fill="none"/></svg>Climbing Gear</li>
    <li><svg viewBox="0 0 10 10"><path d="M1 5l3 3 5-7" stroke="#666" stroke-width="1.6" fill="none"/></svg>Ropes &amp; Cordags</li>
    <li><svg viewBox="0 0 10 10"><path d="M1 5l3 3 5-7" stroke="#666" stroke-width="1.6" fill="none"/></svg>Hydration</li>
    <li><svg viewBox="0 0 10 10"><path d="M1 5l3 3 5-7" stroke="#666" stroke-width="1.6" fill="none"/></svg>Core Tools</li>
    <li><svg viewBox="0 0 10 10"><path d="M1 5l3 3 5-7" stroke="#666" stroke-width="1.6" fill="none"/></svg>Snowshoes</li>
    <li><svg viewBox="0 0 10 10"><path d="M1 5l3 3 5-7" stroke="#666" stroke-width="1.6" fill="none"/></svg>Beacons</li>
    <li><svg viewBox="0 0 10 10"><path d="M1 5l3 3 5-7" stroke="#666" stroke-width="1.6" fill="none"/></svg>Skins</li>
    <li><svg viewBox="0 0 10 10"><path d="M1 5l3 3 5-7" stroke="#666" stroke-width="1.6" fill="none"/></svg>Shovels</li>
    <li><svg viewBox="0 0 10 10"><path d="M1 5l3 3 5-7" stroke="#666" stroke-width="1.6" fill="none"/></svg>Skis</li>
    <li><svg viewBox="0 0 10 10"><path d="M1 5l3 3 5-7" stroke="#666" stroke-width="1.6" fill="none"/></svg>Ski Poles Ski Boots</li>
    <li><svg viewBox="0 0 10 10"><path d="M1 5l3 3 5-7" stroke="#666" stroke-width="1.6" fill="none"/></svg>Snowshoes</li>
    <li><svg viewBox="0 0 10 10"><path d="M1 5l3 3 5-7" stroke="#666" stroke-width="1.6" fill="none"/></svg>Beacons</li>
    <li><svg viewBox="0 0 10 10"><path d="M1 5l3 3 5-7" stroke="#666" stroke-width="1.6" fill="none"/></svg>Skins</li>
  </ul>
</aside>

<h2 class="abs latest" style="font-weight:400">LATEST PORODUCTS</h2>
<svg class="abs arrows" width="20" height="14" viewBox="0 0 20 14"><path d="M7 2L2 7l5 5M13 2l5 5-5 5" stroke="#333" stroke-width="2.4" fill="none"/></svg>

<div class="abs card" style="left:257px;top:449px"><div class="thumb" role="img" aria-label="Orange climbing skin with yellow clip" style="background:linear-gradient(#e07a3a,#c2501e)"></div><h3>Ridgeforge</h3><p>Overall the customer service VPO provided was&nbsp; your</p><div class="price">$ 139.95</div><div class="cart">Add To Cart <svg width="9" height="9" viewBox="0 0 10 10"><path d="M1 3h8l-1 6H2z" fill="#fff"/></svg></div></div>
<div class="abs card" style="left:390px;top:449px"><div class="thumb" role="img" aria-label="Teal hooded hardshell jacket" style="background:linear-gradient(#2a8aa8,#125b74)"></div><h3>Ridgeforge</h3><p>Overall the customer service VPO provided was&nbsp; your</p><div class="price">$ 139.95</div><div class="cart">Add To Cart <svg width="9" height="9" viewBox="0 0 10 10"><path d="M1 3h8l-1 6H2z" fill="#fff"/></svg></div></div>
<div class="abs card" style="left:521px;top:449px"><div class="thumb" role="img" aria-label="White and blue ski boot" style="background:linear-gradient(#e8eef2,#7fc6dc)"></div><h3>Ridgeforge</h3><p>Overall the customer service VPO provided was&nbsp; your</p><div class="price">$ 139.95</div><div class="cart">Add To Cart <svg width="9" height="9" viewBox="0 0 10 10"><path d="M1 3h8l-1 6H2z" fill="#fff"/></svg></div></div>
<div class="abs card" style="left:257px;top:659px"><div class="thumb" role="img" aria-label="Blue and green backpack" style="background:linear-gradient(#3a8ad8,#8cc83a)"></div><h3>Ridgeforge</h3><p>Overall the customer service VPO provided was&nbsp; your</p><div class="price">$ 139.95</div><div class="cart">Add To Cart <svg width="9" height="9" viewBox="0 0 10 10"><path d="M1 3h8l-1 6H2z" fill="#fff"/></svg></div></div>
<div class="abs card" style="left:390px;top:659px"><div class="thumb" role="img" aria-label="Black insulated glove" style="background:linear-gradient(#3a3a3a,#111)"></div><h3>Ridgeforge</h3><p>Overall the customer service VPO provided was&nbsp; your</p><div class="price">$ 139.95</div><div class="cart">Add To Cart <svg width="9" height="9" viewBox="0 0 10 10"><path d="M1 3h8l-1 6H2z" fill="#fff"/></svg></div></div>
<div class="abs card" style="left:521px;top:659px"><div class="thumb" role="img" aria-label="Amber lens ski goggles" style="background:linear-gradient(#e8b43a,#9a6a14)"></div><h3>Ridgeforge</h3><p>Overall the customer service VPO provided was&nbsp; your</p><div class="price">$ 139.95</div><div class="cart">Add To Cart <svg width="9" height="9" viewBox="0 0 10 10"><path d="M1 3h8l-1 6H2z" fill="#fff"/></svg></div></div>

<h2 class="abs brands-title" style="font-weight:400">Our Brands</h2>
<div class="abs brands">
  <span class="brand" style="color:#c0141c"><i style="background:#c0141c;border-radius:50%"></i>Talusmark</span>
  <span class="brand" style="color:#c0141c">Korvo</span>
  <span class="brand" style="color:#9a1a1a"><i style="background:#9a1a1a"></i>Vexa</span>
  <span class="brand" style="color:#1e4f8c">Brunnel</span>
  <span class="brand" style="color:#d8262c">Kestrel</span>
  <span class="brand" style="color:#d9a82a">Summit Forge</span>
  <span class="brand" style="color:#1a8ab8"><i style="background:#1a8ab8"></i>Pellino</span>
</div>

<footer class="abs footer">
  <div class="fcol" style="left:101px"><h4>Menu</h4><ul><li>Rescue Gear</li><li>Footwear</li><li>Clothing</li><li>Sleeping Bags</li><li>Camping Gear</li><li>Snow Sports</li><li>Brands</li></ul></div>
  <div class="fcol" style="left:194px"><h4>Products</h4><ul><li>Snowshoes</li><li>Beacons</li><li>Skins</li><li>Shovels</li><li>Skis</li><li>Ski Poles Ski Boots</li></ul></div>
  <div class="fcol" style="left:287px"><h4>Newsletters</h4><p>All the Lorem Ipsum generators on the<br>Internet&nbsp; on the Internet.</p><div class="field">Your Name :</div><div class="field">Password :</div><div class="submit">SUBMIT</div></div>
  <div class="fcol" style="left:443px"><h4>Contact Us</h4><p>Call now :<br>1800 420 117</p><p style="margin-top:4px">Address :<br>214 Harbour Trade Centre, Beside<br>Lakeview Clinic, Ridge Road,<br>Halden, Canada,</p></div>
  <div class="fcol" style="left:568px"><h4>Follow Us</h4><div class="social"><i></i>Linkwall</div><div class="social"><i></i>Chirper</div><div class="social"><i></i>Circlecast</div><div class="social"><i></i>Rss</div></div>
</footer>
<div class="abs copy">Copyright 2014 Northvale.All Right Reseved.</div>
</body>
</html>
```